Small Business Consulting Firm Needs Letterhead

We need a letterhead for our company "Brightpath Plus". Our company does outbound calling and mailing to business owner's companies who have taken high interest loans. These loans tend to put these businesses in a big financial bind short term, and we help them find better financial options. We would like the design to match our colors of our logo. Headers and footers would look nice, but we are open. We would want it to include our address, website, phone, and email info. Our address - 2000 E. Lamar Blvd. Suite 600Website - www.safeguardtoday.comEmail - info@safeguardtoday.comPhone - 855-726-1938
Industry/Entity Type
Financial Planning
Look and feel
Each slider illustrates characteristics of the customer's brand and the style your logo design should communicate.

```html
<!DOCTYPE html>
<html lang="en">
<head>
<meta charset="utf-8">
<title>Brightpath Plus Letterhead</title>
<link rel="stylesheet" href="https://fonts.googleapis.com/css2?family=Open+Sans:wght@400&family=Roboto:wght@400&display=swap">
<style>
  :root {
    --backdrop: #e4e4e4;
    --paper: #f7f7f7;
    --ink: #555555;
    --brand-blue: #0a72bf;
    --brand-green: #6bb33c;
    --contact-ink: #4a4a4a;
    --signature-tone: #d9d9d9;
  }
  * { margin: 0; padding: 0; box-sizing: border-box; }
  html, body {
    width: 1200px; height: 1108px; overflow: hidden;
    background: var(--backdrop);
  }
  .letterhead {
    position: absolute; left: 223px; top: 20px;
    width: 753px; height: 1068px;
    background: var(--paper);
    box-shadow: 0 2px 10px rgba(0,0,0,.18);
    font-family: "Open Sans", sans-serif;
    color: var(--ink);
  }
  .brand {
    position: absolute; left: 67px; top: 78px;
    display: flex; align-items: center; gap: 10px;
  }
  .brand-mark { width: 16px; height: 16px; background: var(--brand-green); }
  .brand-name {
    font-family: "Open Sans", sans-serif; font-size: 19px; font-weight: 400;
    letter-spacing: .6px; text-transform: uppercase; color: #3b3b3b;
  }
  .contact {
    position: absolute; right: 75px; top: 56px; text-align: right;
    font-family: "Roboto", sans-serif; color: var(--contact-ink);
  }
  .contact-address { font-size: 14.5px; margin-bottom: 6px; }
  .contact-line {
    display: flex; justify-content: flex-end; align-items: center; gap: 5px;
    font-size: 13.5px; line-height: 19px;
  }
  .contact-icon { width: 12px; height: 12px; }
  .letter-body {
    position: absolute; left: 62px; top: 282px; width: 616px;
    font-size: 14.2px; line-height: 20.3px;
  }
  .letter-body p { margin-bottom: 20.3px; text-align: justify; }
  .letter-body .salutation, .letter-body .closing { text-align: left; }
  .signature {
    width: 90px; height: 82px; margin-top: 6px;
    background: var(--signature-tone); border-radius: 4px;
  }
  .footer-band { position: absolute; left: 0; bottom: 0; width: 753px; height: 26px; }
  .footer-web {
    position: absolute; right: 53px; bottom: 5px;
    font-family: "Roboto", sans-serif; font-size: 14px; color: #ffffff;
  }
</style>
</head>
<body>
  <main class="letterhead">
    <header>
      <div class="brand">
        <span class="brand-mark"></span>
        <span class="brand-name">Brightpath Plus</span>
      </div>
      <div class="contact">
        <div class="contact-address">4170 W. Corwin Ave. Suite 310</div>
        <div class="contact-line">855-726-1938
          <svg class="contact-icon" viewBox="0 0 24 24" aria-hidden="true"><path fill="var(--brand-green)" d="M6.6 10.8a15.1 15.1 0 0 0 6.6 6.6l2.2-2.2c.3-.3.7-.4 1-.2 1.1.4 2.3.6 3.6.6.6 0 1 .4 1 1V20c0 .6-.4 1-1 1A17 17 0 0 1 3 4c0-.6.4-1 1-1h3.5c.6 0 1 .4 1 1 0 1.3.2 2.5.6 3.6.1.3 0 .7-.2 1z"/></svg>
        </div>
        <div class="contact-line">info@brightpathplus.com
          <svg class="contact-icon" viewBox="0 0 24 24" aria-hidden="true"><rect x="2" y="5" width="20" height="14" fill="var(--brand-green)"/><path d="M2 5l10 8 10-8" fill="none" stroke="#fff" stroke-width="1.6"/></svg>
        </div>
      </div>
    </header>

    <section class="letter-body">
      <p class="salutation">Dear customer,</p>
      <p>Lorem ipsum dolor sit amet, consectetur adipisicing elit, sed do eiusmod tempor incididunt ut labore et dolore magna aliqua. Ut enim ad minim veniam, quis nostrud exercitation ullamco laboris nisi ut aliquip ex ea commodo consequat. Duis aute irure dolor in reprehenderit in voluptate velit esse cillum dolore eu fugiat nulla pariatur. Excepteur sint occaecat cupidatat non proident, sunt in culpa qui officia deserunt mollit anim id est laborum.</p>
      <p>Lorem ipsum dolor sit amet, consectetur adipisicing elit, sed do eiusmod tempor incididunt ut labore et dolore magna aliqua. Ut enim ad minim veniam, quis nostrud exercitation ullamco laboris nisi ut aliquip ex ea commodo consequat. Duis aute irure dolor in reprehenderit in voluptate velit esse cillum dolore eu fugiat nulla pariatur. Excepteur sint occaecat cupidatat non proident, sunt in culpa qui officia deserunt mollit anim id est laborum.</p>
      <p>Lorem ipsum dolor sit amet, consectetur adipisicing elit, sed do eiusmod tempor incididunt ut labore et dolore magna aliqua. Ut enim ad minim veniam, quis nostrud exercitation ullamco laboris nisi ut aliquip ex ea commodo consequat. Duis aute irure dolor in reprehenderit in voluptate velit esse cillum dolore eu fugiat nulla pariatur. Excepteur sint occaecat cupidatat non proident, sunt in culpa qui officia deserunt mollit anim id est laborum.</p>
      <p>Lorem ipsum dolor sit amet, consectetur adipisicing elit, sed do eiusmod tempor incididunt ut labore et dolore magna aliqua. Ut enim ad minim veniam, quis nostrud exercitation ullamco laboris nisi ut aliquip ex ea commodo consequat. Duis aute irure dolor in reprehenderit.</p>
      <p class="closing">Yours Sincerely,</p>
      <div class="signature" role="img" aria-label="Handwritten signature of the sender"></div>
    </section>

    <footer>
      <svg class="footer-band" viewBox="0 0 753 26" aria-hidden="true">
        <polygon points="0,11 484,11 474,26 0,26" fill="var(--brand-blue)"/>
        <polygon points="482,26 499,0 753,0 753,26" fill="var(--brand-green)"/>
      </svg>
      <div class="footer-web">www.brightpathplus.com</div>
    </footer>
  </main>
</body>
</html>
```